tallow-brook.com

We are a small dollar lending company that will revolutionize the industry. We will do this by being completely transparent, fee free, etc and an interest rate that normal people can afford to pay. Over 10X less than our competition. We only allow our members to pay bills " bills paid fast", within 72 hours. Payday loans typically charge from 390%-600% with a terrible payback structure. We charge 36%, period, with a payback structure over 12 months. Our site will be very simple and easy to use but elegant at the same time. We do not want the site to be too busy, less is more and easier. We will have; Home, The Story, Why tallowbrook.com, Are you eligible? Members, Clients. To become a member you have to be referred by a current client of tallowbrook.com. A lot of the busy stuff will be saved for the Members and Clients sections. The feel must be elegant, easy to use and very simple to understand. I am looking for the green, white and black combinations of colors, very similar to my logo that was designed by Fernquillo.

```html
<!DOCTYPE html>
<html lang="en">
<head>
<meta charset="utf-8">
<title>tallow-brook.com</title>
<link href="https://fonts.googleapis.com/css2?family=Open+Sans:wght@400;600;700&family=Arimo:wght@400&display=swap" rel="stylesheet">
<style>
:root{
  --green:#6cbf2c;
  --green-light:#9ed35a;
  --green-dark:#3e9a14;
  --ink:#222;
  --text:#444;
  --grey-band:#e8e8e8;
  --white:#fff;
}
*{box-sizing:border-box;margin:0;padding:0}
html,body{width:834px;height:1200px;overflow:hidden}
body{font-family:"Open Sans",Arial,sans-serif;color:var(--text);background:var(--white);position:relative}
.abs{position:absolute}

.header{top:0;left:0;width:834px;height:91px;background:#f7f7f7}
.brand{left:121px;top:19px;display:flex;align-items:center;gap:10px}
.brand-mark{width:56px;height:56px;border-radius:6px;background:linear-gradient(#8fd040,#4aa91a)}
.brand-name{font-size:24px;font-weight:600;color:#111;letter-spacing:-.5px}
.call{left:489px;top:41px;font-size:12px;color:#222}
.call span{color:var(--green)}
.login{left:616px;top:37px;width:96px;height:25px;background:#3a3a3a;border-radius:2px;color:#fff;font-size:12px;display:flex;align-items:center}
.login .ico{width:22px;height:25px;display:flex;align-items:center;justify-content:center;background:#2a2a2a;margin-right:18px}

.nav{top:91px;left:0;width:834px;height:50px;background:linear-gradient(#a6d85f,#74c232)}
.nav ul{list-style:none;display:flex;position:absolute;left:121px;top:0;height:50px}
.nav li{color:#fff;font-size:11px;padding:0 16px;line-height:50px;border-right:1px solid rgba(255,255,255,.35)}
.nav li.active{background:#3a3a3a}
.nav li:last-child{border-right:none}

.hero{top:141px;left:0;width:834px;height:416px;background:linear-gradient(120deg,#c9b4a0 0%,#dfe6ea 35%,#b9d4e4 70%,#d4e6ef 100%)}
.hero-caption{left:445px;top:416px;width:271px;height:57px;background:rgba(40,40,40,.85);color:#fff;font-size:29px;line-height:57px;text-align:center;font-weight:400}
.slider{left:355px;top:520px;width:107px;height:17px;background:#f4f4f4;border:1px solid #bbb;border-radius:3px;display:flex;align-items:center;padding-left:6px;gap:5px}
.slider .dot{width:5px;height:5px;border-radius:50%;background:#aaa}
.slider .dot.on{background:#222}
.slider .arrows{font-size:9px;color:#333;width:24px;border-right:1px solid #ccc;margin-right:2px}

.features{top:557px;left:0;width:834px;height:143px;background:linear-gradient(#f0f4f6,#d6dadd)}
.feature{top:47px;display:flex;align-items:center;gap:9px}
.feature .circle{width:54px;height:54px;border-radius:50%;background:#fff;box-shadow:0 1px 3px rgba(0,0,0,.3);display:flex;align-items:center;justify-content:center}
.feature h3{color:var(--green);font-size:12px;font-weight:700;letter-spacing:.3px}
.feature p{font-size:9px;color:#333;margin-top:2px}
.feature .more{font-size:7.5px;font-weight:600;color:#333;margin-top:3px}

.welcome-title{left:124px;top:729px;font-size:13.5px;font-weight:600;color:#222}
.welcome-photo{left:122px;top:760px;width:196px;height:117px;background:linear-gradient(135deg,#c9a58a,#e9e7e4 50%,#444 85%)}
.welcome-text{left:325px;top:757px;width:178px;font-size:7.6px;line-height:13.6px;letter-spacing:-.1px;text-align:justify;color:#444}
.btn-more{left:325px;top:861px;width:59px;height:16px;background:var(--green);color:#fff;font-size:8px;text-align:center;line-height:16px;border-radius:2px}
.promise{left:520px;top:760px;width:195px;height:118px;background:linear-gradient(#9ed35a,#6cbf2c);color:#fff;font-size:11px;line-height:22px;padding:12px 15px;text-align:justify;text-align-last:center}
.promise .lead{font-size:13px;display:block;text-align-last:justify}

.clients{top:922px;left:0;width:834px;height:71px;background:#f5f5f5}
.clients-label{left:123px;top:24px;font-size:10.5px;line-height:12px;color:#333;letter-spacing:-.3px}
.clients-row{left:212px;top:10px;width:497px;height:47px;background:#ececec;display:flex;align-items:center;justify-content:space-around;color:#9a9a9a;font-weight:700}

.links{top:993px;left:0;width:834px;height:110px;background:var(--grey-band);font-family:Arimo,Arial,sans-serif}
.col{top:21px}
.col h4{font-size:11px;font-weight:400;color:#333;margin-bottom:12px;padding-bottom:3px;border-bottom:1px solid #ddd;width:110px}
.col li{list-style:none;font-size:7.2px;color:#333;line-height:13px}

.footer{top:1103px;left:0;width:834px;height:97px;background:linear-gradient(#4aa91a,#6cbf2c)}
.foot-brand{left:121px;top:30px;display:flex;align-items:center;gap:8px;color:#fff;font-size:18px}
.foot-brand .mark{width:30px;height:30px;border-radius:50%;border:3px solid #fff}
.social{left:552px;top:28px;display:flex;gap:5px}
.social span{width:24px;height:24px;border-radius:50%;background:#fff;opacity:.92}
.copy{left:565px;top:65px;font-family:Arimo,Arial,sans-serif;font-size:8px;color:#fff}
</style>
</head>
<body>

<header class="header abs">
  <div class="brand abs"><div class="brand-mark"></div><div class="brand-name">TALLOW BROOK</div></div>
  <div class="call abs"><span>CALL :</span> 250-555-0143</div>
  <div class="login abs"><div class="ico"><svg width="10" height="11" viewBox="0 0 10 11"><circle cx="5" cy="3" r="2.6" fill="#fff"/><path d="M0 11c0-3.5 2-5 5-5s5 1.5 5 5z" fill="#fff"/></svg></div>LOG IN</div>
</header>

<nav class="nav abs">
  <ul>
    <li class="active">HOME</li><li>THE STORY</li><li>WHY TALLOWBROOK.COM</li><li>ARE YOU ELIGIBLE? MEMBERS</li><li>CLIENTS</li>
  </ul>
</nav>

<section class="hero abs" role="img" aria-label="Photo of a hand counting out dollar bills beside stacks of cash on a desk"></section>
<div class="hero-caption abs">BILLS PAID FAST</div>
<div class="slider abs"><div class="arrows">&lsaquo; &rsaquo;</div><span class="dot"></span><span class="dot"></span><span class="dot on"></span><span class="dot"></span><span class="dot"></span><span class="dot"></span></div>

<section class="features abs">
  <div class="feature abs" style="left:123px">
    <div class="circle"><svg width="24" height="28" viewBox="0 0 24 28"><rect x="1" y="1" width="22" height="26" rx="2" fill="none" stroke="#5bb31f" stroke-width="2"/><rect x="5" y="5" width="14" height="5" fill="#5bb31f"/><rect x="5" y="13" width="6" height="5" fill="#5bb31f"/><rect x="13" y="13" width="6" height="5" fill="#5bb31f"/><rect x="5" y="20" width="6" height="4" fill="#5bb31f"/><rect x="13" y="20" width="6" height="4" fill="#5bb31f"/></svg></div>
    <div><h3>CALCULATE</h3><p>Dipisicing elit sed do eiusmod</p><div class="more">READ MORE</div></div>
  </div>
  <div class="feature abs" style="left:328px">
    <div class="circle"><svg width="26" height="28" viewBox="0 0 26 28"><circle cx="13" cy="9" r="8" fill="none" stroke="#5bb31f" stroke-width="2"/><text x="13" y="13" font-size="11" font-weight="700" fill="#5bb31f" text-anchor="middle" font-family="Open Sans,sans-serif">$</text><path d="M2 27c0-6 5-8 11-8s11 2 11 8z" fill="#5bb31f"/></svg></div>
    <div><h3>ARE YOU ELIGIBLE</h3><p>Dipisicing elit sed do eiusmod</p><div class="more">READ MORE</div></div>
  </div>
  <div class="feature abs" style="left:534px">
    <div class="circle"><svg width="28" height="22" viewBox="0 0 28 22"><rect x="2" y="5" width="24" height="14" rx="1" fill="#5bb31f" transform="rotate(-12 14 12)"/><circle cx="16" cy="11" r="4" fill="#fff"/></svg></div>
    <div><h3>PAY BILLS</h3><p>Dipisicing elit sed do eiusmod</p><div class="more">READ MORE</div></div>
  </div>
</section>

<h2 class="welcome-title abs">WELCOME TO TALLOW-BROOK</h2>
<div class="welcome-photo abs" role="img" aria-label="Photo of hands working a calculator over paperwork"></div>
<p class="welcome-text abs">Lorem ipsum dolor sit amet, consectetur adipisicing elit, sed do eiusmod Incididunt ut labore et dolore magna aliqua. Ut enim ad minim veniam, quis nostrud exercitation ullamco laboris nisi ut aliquip ex ea commodo consequat. Duis aute irure dolor in reprehenderit in voluptate velit esse cillum dolore eu fugiat nulla pariatur.</p>
<div class="btn-more abs">Read More</div>
<div class="promise abs"><span class="lead">WE CHARGE ONLY 36%</span>AND GIVE OVER 12 MONTHS TIME TO PAY BACK, NO FEES, HIDDEN COSTS ETC.</div>

<section class="clients abs">
  <div class="clients-label abs">OUR MOST<br>RECENT CLIENTS</div>
  <div class="clients-row abs">
    <span style="font-size:20px;color:#777">NORVALE</span>
    <span style="font-size:26px;color:#888">KT19</span>
    <span style="font-size:14px">BRIMWORKS</span>
    <span style="font-size:15px">OAKLET</span>
    <span style="font-size:14px">HALVARD</span>
  </div>
</section>

<section class="links abs">
  <div class="col abs" style="left:124px"><h4>How We Help</h4><ul><li>Lead Generation</li><li>Tactics Management</li><li>Start-Up Website</li><li>Website Facelifts</li></ul></div>
  <div class="col abs" style="left:297px"><h4>Services</h4><ul><li>Social Media Coaching</li><li>Website Analysis</li><li>Quillet Website Design</li><li>Newsletters</li></ul></div>
  <div class="col abs" style="left:469px"><h4>Results</h4><ul><li>Testimonials</li><li>B2B Companies</li><li>Contractors &amp; Construction</li><li>Manufacturing</li></ul></div>
  <div class="col abs" style="left:637px"><h4>Support</h4><ul><li>Why Choose Pellmar</li><li>Our Culture</li><li>Our Team</li><li>Sitemap</li></ul></div>
</section>

<footer class="footer abs">
  <div class="foot-brand abs"><div class="mark"></div>TALLOW BROOK</div>
  <div class="social abs"><span></span><span></span><span></span><span></span><span></span><span></span></div>
  <div class="copy abs">Copy Right &copy; 2014. All rights reserved.</div>
</footer>

</body>
</html>
```